New business card for a regional office of a US M&A company

We need business card for a finance company, office based in Hong Kong , our Head office is in US, our business is to Merge and acquires companies , the new office will be a regional office for the Asia Pacific region. We want to use the head office logo as attached ( but don't have to be exactly the same, can be a variation to it) as a base and then add Asia Pacific alongside the logo.
We would prefer to have be bilingual Eng + Chinese, although we don't really have Chinese company name .

Industry/Entity Type

Business

Contact Information for Business Card

Clara Jo Tsang
 

VP,
APAC M&A Operations
Orin Vantage Asia Pacific Limited
 
Unit 1407, K18
18 Tai Lok Shan Road, 
Hong Kong 
 
M: +852 6038 1742
T : +852 2836 4100
F : +852 2836 4177
VOIP: 4158
 
cjtsang@orinvantage.com

Font styles to use
Serif
Sans Serif

Colors

Designer to choose colors to be used in the design.

Requirements
Must have
• APAC Office

```html
<!DOCTYPE html>
<html lang="en">
<head>
<meta charset="utf-8">
<title>Orin Vantage Asia Pacific – Business Card</title>
<link rel="stylesheet" href="https://fonts.googleapis.com/css2?family=Arimo:wght@700&family=Source+Sans+3:wght@400&display=swap">
<style>
  :root {
    --navy: #0f2a44;
    --cyan: #1ea5d4;
    --paper: #f4f3f1;
    --stage: #dcdcdc;
    --white: #ffffff;
  }
  html, body {
    margin: 0;
    width: 1200px;
    height: 900px;
    overflow: hidden;
    background: var(--stage);
  }
  .card {
    position: absolute;
    left: 120px;
    top: 154px;
    width: 960px;
    height: 592px;
    background: var(--paper);
    box-shadow: 0 6px 24px rgba(0,0,0,0.15);
    overflow: hidden;
  }
  .card__panel {
    position: absolute;
    inset: 0;
  }
  .card__name {
    position: absolute;
    left: 54px;
    top: 64px;
    margin: 0;
    font: 700 26px/1 "Arimo", sans-serif;
    color: var(--white);
    letter-spacing: 0.3px;
    text-transform: uppercase;
  }
  .card__role {
    position: absolute;
    left: 54px;
    top: 100px;
    margin: 0;
    font: 400 25px/1 "Source Sans 3", sans-serif;
    color: var(--white);
  }
  .contacts {
    position: absolute;
    left: 58px;
    top: 243px;
    margin: 0;
    padding: 0;
    list-style: none;
    font: 400 25px/35px "Source Sans 3", sans-serif;
    color: var(--white);
  }
  .contacts li {
    display: flex;
    align-items: center;
    height: 35px;
  }
  .contacts svg {
    width: 20px;
    height: 20px;
    margin-right: 12px;
    fill: var(--white);
  }
  .address {
    position: absolute;
    left: 54px;
    top: 400px;
    margin: 0;
    font: 400 25px/35px "Source Sans 3", sans-serif;
    font-style: normal;
    color: var(--white);
  }
  .address__company {
    display: block;
    font-size: 26px;
    text-transform: uppercase;
  }
  .voip {
    position: absolute;
    right: 50px;
    top: 56px;
    margin: 0;
    font: 700 25px/1 "Arimo", sans-serif;
    color: var(--navy);
  }
  .voip__number { color: var(--cyan); }
  .brand {
    position: absolute;
    left: 560px;
    top: 350px;
    width: 370px;
    text-align: center;
  }
  .brand__square {
    display: block;
    width: 84px;
    height: 84px;
    margin: 0 auto 70px;
    background: var(--navy);
  }
  .brand__name {
    font: 700 23px/1 "Arimo", sans-serif;
    color: var(--cyan);
    text-transform: uppercase;
    white-space: nowrap;
  }
</style>
</head>
<body>
  <article class="card">
    <svg class="card__panel" width="960" height="592" viewBox="0 0 960 592" aria-hidden="true">
      <polygon points="0,0 380,0 612,296 380,592 0,592" fill="var(--cyan)"/>
      <polygon points="0,0 366,0 598,296 366,592 0,592" fill="var(--navy)"/>
    </svg>

    <h1 class="card__name">Clara Jo Tsang VP</h1>
    <p class="card__role">APAC M&amp;A Operations</p>

    <ul class="contacts">
      <li>
        <svg viewBox="0 0 20 20"><path d="M2 8c0-3 3-5 8-5s8 2 8 5v2h-4V8H6v2H2z M5 11h10l2 6H3z"/></svg>
        +852 2836 4100
      </li>
      <li>
        <svg viewBox="0 0 20 20"><path d="M6 1h8a1 1 0 0 1 1 1v16a1 1 0 0 1-1 1H6a1 1 0 0 1-1-1V2a1 1 0 0 1 1-1zm1 2v12h6V3zm3 13a1 1 0 1 0 0 2 1 1 0 0 0 0-2z"/></svg>
        +852 6038 1742
      </li>
      <li>
        <svg viewBox="0 0 20 20"><path d="M5 2h8l2 2v4h2a1 1 0 0 1 1 1v9H2V9a1 1 0 0 1 1-1h2zm2 2v4h6V5h-1V4zm-2 7v2h2v-2zm4 0v2h2v-2zm4 0v2h2v-2z"/></svg>
        +852 2836 4177
      </li>
      <li>
        <svg viewBox="0 0 20 20"><path d="M2 5h16v10H2zm1.5 1.2v.4L10 11l6.5-4.4v-.4z"/></svg>
        cjtsang@orinvantage.com
      </li>
    </ul>

    <address class="address">
      <span class="address__company">Orin Vantage Asia Pacific Ltd</span>
      Unit 1407, K18<br>
      18 Tai Lok Shan Road,<br>
      Hong Kong
    </address>

    <p class="voip">VOIP: <span class="voip__number">4158</span></p>

    <div class="brand">
      <span class="brand__square"></span>
      <span class="brand__name">Orin Vantage Asia Pacific</span>
    </div>
  </article>
</body>
</html>
```